Lantern Petals Website v.1 - attract floral shop franchisees

I need a simple information website for my new business. We are a franchisor of flower shops. The overall purpose of the website is to promote the company and the service, especially to potential franchisees and retailers. Only about 4 pages are required including homepage, About, For Supermarkets, For Franchisees, and Contact. No special functions are required except the site will have two separate inquiry forms that must be filled out online and submitted via automated email. Similarly, an email form should be linked from the Contact page. I have a logo and business cards designed by ArtMingle, and I would like the site to have a consistent color scheme and style. The key to design will be to express the joy and love associated with flowers and floral bouquets.
IMPORTANT - I will be exporting the website design to Wordpress CMS in a site hosted by HostNimbus. For smooth integration into WordPress hosted by HostNimbus, the designer should build the site using a WordPress-friendly format. Ideally, they should use HTML, CSS, and PHP. Creating a custom theme or using a page builder that exports to WordPress-compatible files is best. This ensures the site can be easily imported and managed within WordPress.

Target Market(s)

Potential franchisees (existing florists or creative types who might like to own a floral business) and supermarkets who might want us to run their floral department

Industry/Entity Type

Floral retailing

Requirements
Must have
• A brand theme that is beautiful, consistent throughout and builds on the logo design
Nice to have
• Show gender and ethnic diversity in customers and florists. Pictures of happy florists (for franchisees) and pictures of amazing floral department displays (for supermarkets)

```html
<!DOCTYPE html>
<html lang="en">
<head>
<meta charset="utf-8">
<title>Lantern Petals</title>
<link href="https://fonts.googleapis.com/css2?family=Jost:wght@300;400;500;600&display=swap" rel="stylesheet">
<style>
:root{
  --green:#05914a;
  --green-dark:#047a3e;
  --orange:#f2ae2e;
  --text:#555;
  --dark:#222;
  --white:#fff;
  --card:#f3f3f3;
}
*{margin:0;padding:0;box-sizing:border-box}
html,body{width:1200px;height:3251px;overflow:hidden}
body{position:relative;background:var(--white);font-family:'Jost',sans-serif;color:var(--text)}
.abs{position:absolute}
.shapes{position:absolute;left:0;top:0}
.top-line{left:0;top:0;width:1200px;height:4px;background:var(--green)}
.pill{top:0;height:40px;border-radius:0 0 22px 22px;color:var(--white);font-size:13px;display:flex;align-items:center;justify-content:center;gap:12px}
.pill svg{width:12px;height:12px;fill:var(--white)}
.pill-call{left:559px;width:250px;background:var(--green);border-radius:0 0 22px 22px}
.pill-mail{left:776px;width:280px;background:var(--orange)}
.brand{left:144px;top:36px;display:flex;align-items:center;gap:10px;font-size:22px;font-weight:500;color:var(--green)}
.brand .dot{width:22px;height:22px;border-radius:50%;background:var(--orange)}
.nav{left:418px;top:66px;display:flex;gap:28px;font-size:13px;color:var(--dark);letter-spacing:.2px}
.btn{display:flex;align-items:center;justify-content:center;border:2px solid var(--orange);border-radius:22px;font-size:12.5px;font-weight:500;color:var(--dark);background:var(--white)}
.btn-nav{left:933px;top:57px;width:122px;height:37px}
.hero-title{left:144px;top:172px;font-weight:400;color:var(--green);line-height:1}
.hero-title .l1{font-size:54px;color:var(--orange);font-weight:300;display:block}
.hero-title .l2{font-size:58px;display:block;margin-top:10px}
.btn-hero{left:148px;top:316px;width:122px;height:38px}
.hero-photo{left:480px;top:100px;width:600px;height:556px;border-radius:48% 52% 45% 55%/55% 45% 55% 45%;background:radial-gradient(ellipse at 50% 55%,#e9728c 0%,#f0a3b0 30%,#9cc66b 55%,#eef1e4 75%,rgba(255,255,255,0) 100%)}
.dots{left:1123px;top:289px;display:flex;flex-direction:column;gap:44px}
.dots span{width:12px;height:12px;border-radius:50%;background:#cfcfcf}
.dots span.on{background:var(--green);box-shadow:0 0 0 3px var(--orange)}
.about-photo{left:132px;top:808px;width:385px;height:454px;border-radius:50%;background:radial-gradient(ellipse at 50% 40%,#e0456f 0%,#c960b0 25%,#f6e9c4 55%,rgba(255,255,255,0) 75%)}
h2{font-weight:400;line-height:1}
.about-h{left:615px;top:826px;font-size:46px;color:var(--green)}
.about-text{left:615px;top:884px;width:440px;font-size:13.5px;line-height:20px;text-align:justify}
.about-text p+p{margin-top:20px}
.btn-about{left:615px;top:1179px;width:123px;height:38px}
.super{left:0;top:1329px;width:1200px;height:666px;background:linear-gradient(100deg,var(--green-dark) 0%,var(--green) 45%,var(--green) 100%)}
.super-h{left:0;width:1200px;top:1425px;text-align:center;font-size:42px;color:var(--white)}
.super-text{left:202px;top:1482px;width:796px;text-align:center;color:var(--white);font-size:13.5px;line-height:20px}
.list{list-style:none}
.list li{display:flex;gap:14px;font-size:13.5px;line-height:20px;margin-bottom:20px}
.list svg{flex:none;width:18px;height:18px;margin-top:1px}
.super-list{left:158px;top:1572px;width:380px;color:var(--white)}
.super-list svg{fill:var(--white)}
.btn-super{left:160px;top:1893px;width:124px;height:38px;background:transparent;color:var(--white)}
.arch-line{left:660px;top:1571px;width:360px;height:424px;border:2px solid var(--orange);border-bottom:none;border-radius:180px 180px 0 0}
.arch-photo{left:633px;top:1571px;width:363px;height:424px;border-radius:182px 182px 0 0;background:linear-gradient(160deg,#6b5a4c 0%,#d7c5c0 35%,#e8a7b6 55%,#4f6b46 80%,#7b5645 100%)}
.fr-h{left:145px;top:2082px;font-size:44px;color:var(--green)}
.fr-text{left:145px;top:2137px;width:910px;font-size:13.5px;line-height:20px;text-align:justify}
.fr-photo{left:139px;top:2234px;width:441px;height:429px;border-radius:50%;background:radial-gradient(ellipse at 50% 40%,#e23a55 0%,#f28aa8 25%,#f6e9c4 55%,rgba(255,255,255,0) 75%)}
.fr-list{left:625px;top:2238px;width:400px}
.fr-list svg{fill:var(--green)}
.btn-fr{left:625px;top:2582px;width:123px;height:38px}
.contact-card{left:144px;top:2833px;width:915px;height:244px;border-radius:40px;background:linear-gradient(180deg,#f4f4f4,#e9e9e9);box-shadow:0 0 0 4px rgba(255,255,255,.7)}
.contact-h{left:144px;width:915px;top:2896px;text-align:center;font-size:42px;color:var(--green)}
.cta{top:2963px;height:38px;border-radius:20px;color:var(--white);font-size:12.5px;font-weight:500;display:flex;align-items:center;justify-content:center;letter-spacing:.2px}
.cta-new{left:305px;width:260px;background:var(--green)}
.cta-pro{left:586px;width:310px;background:var(--orange)}
.foot-item{top:3124px;display:flex;align-items:center;gap:8px;font-size:17px;color:var(--dark)}
.foot-item .ic{width:30px;height:30px;border-radius:50%;background:var(--green);display:flex;align-items:center;justify-content:center}
.foot-item svg{width:14px;height:14px;fill:var(--white)}
.foot-mail{left:580px}
.foot-phone{left:908px}
.foot-rule{left:485px;top:3179px;width:570px;height:1px;background:#b8862a}
.copy{left:700px;width:355px;top:3203px;text-align:right;font-size:12.5px;color:var(--dark)}
</style>
</head>
<body>
<svg class="shapes" width="1200" height="3251" viewBox="0 0 1200 3251" aria-hidden="true">
  <path d="M0,420 C180,410 380,450 540,560 C700,670 900,740 1185,715 C900,738 720,705 560,640 C420,585 250,548 0,560 Z" fill="var(--orange)"/>
  <path d="M0,575 C150,545 330,560 505,637 C330,592 150,612 0,665 Z" fill="var(--green)"/>
  <path d="M1200,2745 C1000,2755 800,2810 690,2900 L690,3080 C560,3085 420,3110 300,3150 C180,3195 80,3230 0,3251 L1200,3251 Z" fill="var(--orange)"/>
  <path d="M1200,2668 C1000,2680 790,2740 675,2830 L725,2830 C835,2770 1000,2738 1200,2730 Z" fill="var(--green)"/>
</svg>

<div class="abs top-line"></div>
<div class="abs pill pill-call"><svg viewBox="0 0 24 24"><path d="M6.6 10.8a15 15 0 006.6 6.6l2.2-2.2c.3-.3.7-.4 1-.2 1.1.4 2.3.6 3.6.6.6 0 1 .4 1 1V20c0 .6-.4 1-1 1A17 17 0 013 4c0-.6.4-1 1-1h3.5c.6 0 1 .4 1 1 0 1.3.2 2.5.6 3.6.1.3 0 .7-.2 1z"/></svg>Call Us : +.614.552.0187</div>
<div class="abs pill pill-mail"><svg viewBox="0 0 24 24"><path d="M2 5h20v2l-10 6L2 7zM2 9l10 6 10-6v10H2z"/></svg>Mail Us : info@Lantern-Petals.com</div>

<div class="abs brand"><span class="dot"></span>Lantern Petals</div>
<nav class="abs nav"><span>ABOUT US</span><span>FOR SUPERMARKETS</span><span>FOR FRANCHISEES</span><span>CONTACT</span></nav>
<div class="abs btn btn-nav">GET STARTED</div>

<div class="abs hero-photo" role="img" aria-label="Smiling florist holding a large bouquet of pink roses and tulips"></div>
<h1 class="abs hero-title"><span class="l1">Lantern</span><span class="l2">PETALS</span></h1>
<div class="abs btn btn-hero">GET STARTED</div>
<div class="abs dots"><span class="on"></span><span></span><span></span><span></span></div>

<div class="abs about-photo" role="img" aria-label="Bouquet of roses, gerberas and orchids"></div>
<h2 class="abs about-h">ABOUT US</h2>
<div class="abs about-text">
  <p>Fresh flowers convey beauty and love, and in our view should become something every person regularly enjoys. Lantern Petals is an entrepreneurial company created to make top quality fresh flowers and professionally-designed bouquets accessible to every consumer at affordable prices.</p>
  <p>Professional florists typically sell the finest quality stems, design the most beautiful bouquets and provide the finest customer service, but their costs — of floral products, retail spaces, labor and marketing — force them to pass high prices along to customers. Supermarket flower departments benefit from high customer footfall, economies of scale and low pricing, but their quality of stems and bouquets is typically poor, staffing is limited, and staff turnover is high which can result in inefficiency, wastage, poorly merchandised selections and limited service.</p>
</div>
<div class="abs btn btn-about">LEARN MORE</div>

<section class="abs super"></section>
<h2 class="abs super-h">SUPERMARKETS</h2>
<p class="abs super-text">Lantern Petals works with some of the country's largest and most progressive supermarkets to provide franchisee ownership and operation of their strategically important floral departments. Supermarkets find that Lantern Petals is able to improve their financial outcomes, provide attentive customer service and satisfaction, and lift the quality of the entire store environment.</p>
<ul class="abs list super-list">
  <li><svg viewBox="0 0 24 24"><path d="M9 16.2l-4.2-4.2L3.4 13.4 9 19 21 7l-1.4-1.4z"/></svg><span>Enhance floral revenue streams with efficient assortments and new offerings</span></li>
  <li><svg viewBox="0 0 24 24"><path d="M9 16.2l-4.2-4.2L3.4 13.4 9 19 21 7l-1.4-1.4z"/></svg><span>Reduce the costs of operating a floral department</span></li>
  <li><svg viewBox="0 0 24 24"><path d="M9 16.2l-4.2-4.2L3.4 13.4 9 19 21 7l-1.4-1.4z"/></svg><span>Improve the quality, useful life and merchandising of floral products</span></li>
  <li><svg viewBox="0 0 24 24"><path d="M9 16.2l-4.2-4.2L3.4 13.4 9 19 21 7l-1.4-1.4z"/></svg><span>Provide attentive customer service, including semi-custom bouquets, by professional florist staff</span></li>
  <li><svg viewBox="0 0 24 24"><path d="M9 16.2l-4.2-4.2L3.4 13.4 9 19 21 7l-1.4-1.4z"/></svg><span>Maintain a beautiful, fresh and well-stocked environment Increase sales and profits</span></li>
  <li><svg viewBox="0 0 24 24"><path d="M9 16.2l-4.2-4.2L3.4 13.4 9 19 21 7l-1.4-1.4z"/></svg><span>Enhance the entire customer shopping environment</span></li>
</ul>
<div class="abs btn btn-super">LEARN MORE</div>
<div class="abs arch-line"></div>
<div class="abs arch-photo" role="img" aria-label="Florist's hands arranging a bouquet with protea on a wooden table"></div>

<h2 class="abs fr-h">FRANCHISEES</h2>
<p class="abs fr-text">Lantern Petals brings the best of professional florists and supermarkets together for the benefit of consumers. It supports a national network of owner-operator franchisees, who in many cases are multi-site professional florists, with comprehensive services to enhance franchise profitability. Lantern Petals works with some of the country's largest and most progressive supermarkets to provide franchisee ownership and operation of their strategically important floral departments.</p>
<div class="abs fr-photo" role="img" aria-label="Bouquet of red and pink lilies and tulips"></div>
<ul class="abs list fr-list">
  <li><svg viewBox="0 0 24 24"><path d="M9 16.2l-4.2-4.2L3.4 13.4 9 19 21 7l-1.4-1.4z"/></svg><span>Be an owner, and your own boss</span></li>
  <li><svg viewBox="0 0 24 24"><path d="M9 16.2l-4.2-4.2L3.4 13.4 9 19 21 7l-1.4-1.4z"/></svg><span>Attractive earnings potential; paid weekly</span></li>
  <li><svg viewBox="0 0 24 24"><path d="M9 16.2l-4.2-4.2L3.4 13.4 9 19 21 7l-1.4-1.4z"/></svg><span>No experience necessary, we set you up to operate and provide extensive support</span></li>
  <li><svg viewBox="0 0 24 24"><path d="M9 16.2l-4.2-4.2L3.4 13.4 9 19 21 7l-1.4-1.4z"/></svg><span>Professional training provided, and a path to floral design industry certification</span></li>
  <li><svg viewBox="0 0 24 24"><path d="M9 16.2l-4.2-4.2L3.4 13.4 9 19 21 7l-1.4-1.4z"/></svg><span>Low operating and supply costs which leverage supermarket economies</span></li>
  <li><svg viewBox="0 0 24 24"><path d="M9 16.2l-4.2-4.2L3.4 13.4 9 19 21 7l-1.4-1.4z"/></svg><span>Affordable franchise fees and low initial investment</span></li>
  <li><svg viewBox="0 0 24 24"><path d="M9 16.2l-4.2-4.2L3.4 13.4 9 19 21 7l-1.4-1.4z"/></svg><span>Opportunities to expand to different locations</span></li>
</ul>
<div class="abs btn btn-fr">LEARN MORE</div>

<div class="abs contact-card"></div>
<h2 class="abs contact-h">CONTACT US</h2>
<div class="abs cta cta-new">NEW FLORIST FRANCHISE INQUIRY</div>
<div class="abs cta cta-pro">PROFESSIONAL FLORIST FRANCHISE INQUIRY</div>

<div class="abs foot-item foot-mail"><span class="ic"><svg viewBox="0 0 24 24"><path d="M2 5h20v2l-10 6L2 7zM2 9l10 6 10-6v10H2z"/></svg></span>info@Lantern-Petals.com</div>
<div class="abs foot-item foot-phone"><span class="ic"><svg viewBox="0 0 24 24"><path d="M6.6 10.8a15 15 0 006.6 6.6l2.2-2.2c.3-.3.7-.4 1-.2 1.1.4 2.3.6 3.6.6.6 0 1 .4 1 1V20c0 .6-.4 1-1 1A17 17 0 013 4c0-.6.4-1 1-1h3.5c.6 0 1 .4 1 1 0 1.3.2 2.5.6 3.6.1.3 0 .7-.2 1z"/></svg></span>+.614.552.0187</div>
<div class="abs foot-rule"></div>
<div class="abs copy">© Copyrights 2024 | All Rights Reserved</div>
</body>
</html>
```